Market leading Turf and Amenity product label design for Fulvic Acid

The product is called Gravimo Total and we are looking for a clean and striking label to go on the front of a 10 litre jerry can, plus a label to fit a small 5kg bucket. The example uploaded is relatively popular and the label is similar to what I would look to use. A visually catching logo would be a must. Key benefits of the product like the example shows would be required.

Target Market(s)

Halvard Division football, golf courses and sports facilities on turf

Requirements
Must have
• A striking title and some limited technical information about the product on the label

examples would be

Enhances plant immunity for better stress management

Enhances photosynthesis and respiration
Prevents NPK nutrients from leaching
Promotes beneficial soil microbes.

```html
<!DOCTYPE html>
<html lang="en">
<head>
<meta charset="utf-8">
<title>Gravimo Total – Jerry Can Label</title>
<link href="https://fonts.googleapis.com/css2?family=Oswald:wght@600&family=Montserrat:wght@400;600;700&display=swap" rel="stylesheet">
<style>
  :root {
    --backdrop: #d4d7de;
    --label-black: #1d1d1d;
    --leaf-green: #8dc63f;
    --leaf-green-deep: #6fa62a;
    --text-white: #ffffff;
    --text-muted: #c9c9c9;
  }
  * { margin: 0; padding: 0; box-sizing: border-box; }
  html, body { width: 1200px; height: 792px; overflow: hidden; background: var(--backdrop); }
  .canvas { position: relative; width: 1200px; height: 792px; }
  .label {
    position: absolute; left: 230px; top: 26px; width: 740px; height: 740px;
    background: var(--label-black); overflow: hidden;
    font-family: "Montserrat", sans-serif; color: var(--text-white);
  }
  .leaf-art { position: absolute; }
  .leaf-art--top {
    left: 0; top: 0; width: 474px; height: 212px;
    background: linear-gradient(180deg, var(--leaf-green) 0%, var(--leaf-green-deep) 100%);
    clip-path: polygon(0 0, 100% 0, 60% 100%, 40% 100%);
    opacity: .9;
  }
  .leaf-art--side {
    left: 383px; top: 0; width: 357px; height: 740px;
    background: linear-gradient(200deg, var(--leaf-green) 0%, var(--leaf-green-deep) 100%);
    clip-path: polygon(60% 0, 100% 0, 100% 100%, 30% 100%, 0 45%);
    opacity: .9;
  }
  .brand { position: absolute; left: 36px; top: 232px; display: flex; align-items: center; gap: 12px; }
  .brand__dot { width: 44px; height: 44px; border-radius: 50%; background: var(--leaf-green); }
  .brand__name { font-weight: 700; font-size: 24px; color: var(--text-white); line-height: 1; }
  .product-title {
    position: absolute; left: 36px; top: 352px;
    font-family: "Oswald", sans-serif; font-weight: 600; line-height: .98;
    text-transform: uppercase; font-size: 82px; letter-spacing: .5px;
  }
  .product-title__first { display: block; color: var(--leaf-green); }
  .product-title__second { display: block; color: var(--text-white); }
  .product-description {
    position: absolute; left: 36px; top: 536px; width: 360px;
    font-size: 10px; line-height: 1.4; color: var(--text-muted);
  }
  .section-heading {
    position: absolute; left: 36px; top: 582px;
    font-size: 22px; font-weight: 600; color: var(--leaf-green); letter-spacing: .5px;
  }
  .benefits { position: absolute; left: 36px; top: 622px; display: flex; gap: 20px; list-style: none; }
  .benefit { display: flex; align-items: center; gap: 6px; width: 76px; font-size: 6.5px; line-height: 1.3; color: var(--text-muted); }
  .benefit svg { flex: none; }
  .application { position: absolute; left: 36px; top: 676px; }
  .application__label { font-size: 15px; font-weight: 700; color: var(--leaf-green); }
  .application__value { font-size: 15px; color: var(--text-white); margin-top: 6px; }
</style>
</head>
<body>
<main class="canvas">
  <section class="label">
    <div class="leaf-art leaf-art--top" role="img" aria-label="Stylised green palm leaf fronds fanning down from the top edge"></div>
    <div class="leaf-art leaf-art--side" role="img" aria-label="Large stylised green palm leaf curving down the right side"></div>

    <div class="brand">
      <span class="brand__dot"></span>
      <span class="brand__name">Verdano Turf Science</span>
    </div>

    <h1 class="product-title">
      <span class="product-title__first">Gravimo</span>
      <span class="product-title__second">Total</span>
    </h1>

    <p class="product-description">100% Naturally extracted formula containing Fulvic, Humic and Amino Acids plus Magnesium and Certorganic listed.</p>

    <h2 class="section-heading">BENEFITS</h2>
    <ul class="benefits">
      <li class="benefit">
        <svg width="20" height="20" viewBox="0 0 20 20"><circle cx="10" cy="10" r="9" fill="none" stroke="#8dc63f" stroke-width="1.2"/><path d="M6 10.5l2.6 2.6L14 7.5" fill="none" stroke="#8dc63f" stroke-width="1.4"/></svg>
        Enhances Plant Immunity For Better Stress Management
      </li>
      <li class="benefit">
        <svg width="20" height="20" viewBox="0 0 20 20"><circle cx="10" cy="10" r="9" fill="none" stroke="#8dc63f" stroke-width="1.2"/><circle cx="10" cy="10" r="3" fill="none" stroke="#8dc63f" stroke-width="1.2"/></svg>
        Enhances Photosynthesis And Respiration
      </li>
      <li class="benefit">
        <svg width="20" height="20" viewBox="0 0 20 20"><circle cx="10" cy="10" r="9" fill="none" stroke="#8dc63f" stroke-width="1.2"/><path d="M10 5v9M6.5 11l3.5 3.5 3.5-3.5" fill="none" stroke="#8dc63f" stroke-width="1.2"/></svg>
        Prevents NPK Nutrients From Leaching
      </li>
      <li class="benefit">
        <svg width="20" height="20" viewBox="0 0 20 20"><circle cx="10" cy="10" r="9" fill="none" stroke="#8dc63f" stroke-width="1.2"/><circle cx="9" cy="9" r="3.5" fill="none" stroke="#8dc63f" stroke-width="1.2"/><path d="M11.5 11.5l3 3" stroke="#8dc63f" stroke-width="1.2"/></svg>
        Promotes Beneficial Soil Microbes
      </li>
    </ul>

    <div class="application">
      <p class="application__label">APPLICATION RATE:</p>
      <p class="application__value">5-10 LITRES PER HECTARE</p>
    </div>
  </section>
</main>
</body>
</html>
```